Web Design Project for a beach town business owner who supports new families with their babies.

I'm looking for a basic website with the following pages: home, about, services, FAQs, blog, and contact page. I have images and content ready to go.

Target Market(s)

Men and women between the ages of 22 and 42, growing families

Industry/Entity Type

Postpartum Doula

Coding

Number of Pages Required

Font styles to use
Serif
Other font styles liked:
• My logo font is "Nexa Bold" - so coordinating fonts with that are ideal

Colors
00AB8E
00BBA5
67D7C9
C6EFE9
E9F9F6
EE7325
F08F49
F5BC92
FAE3D3
FDF4ED

Requirements
Must have
• Warm and professional vibe, multicultural images, aligned with my branding colors and font ("Nexa Bold"; COLORS: light blue hex: #2FCEC2 R: 47 G: 206 B: 194 dark blue hex: #007C7C R: 0 G: 124 B: 124 orange hex: #F77B4E R: 247 G: 123 B: 78), good SEO
Should not have
• Ultra feminine images, baby bottles, cutesy images.

```html
<!DOCTYPE html>
<html lang="en">
<head>
<meta charset="utf-8">
<title>Harborline Families Postpartum Care</title>
<link rel="stylesheet" href="https://fonts.googleapis.com/css2?family=Montserrat:wght@600;700;800&family=Roboto:wght@400;500;700&display=swap">
<style>
:root{
  --teal:#2fcec2;
  --teal-dark:#007c7c;
  --orange:#f77b4e;
  --ink:#1f1f1f;
  --band:#222222;
  --footer:#333333;
  --text:#555555;
  --white:#ffffff;
  --head:"Montserrat",sans-serif;
  --body:"Roboto",sans-serif;
}
*{box-sizing:border-box;margin:0;padding:0}
html,body{width:1200px;height:4238px;overflow:hidden}
body{position:relative;font-family:var(--body);color:var(--text);background:var(--white)}
.abs{position:absolute}
.btn{position:absolute;display:flex;align-items:center;justify-content:center;gap:10px;background:var(--teal);color:var(--white);font:700 14px var(--body);letter-spacing:.3px;outline:2px solid var(--teal);outline-offset:3px;border:2px solid var(--white);text-decoration:none}
.btn svg{width:14px;height:14px}

/* header */
.site-header{position:absolute;left:0;top:0;width:1200px;height:87px;background:var(--white);z-index:2}
.brand{position:absolute;left:104px;top:4px;width:126px;height:126px;border-radius:50%;background:var(--white);display:flex;align-items:center;justify-content:center;z-index:3}
.brand span{width:104px;height:104px;border-radius:50%;border:3px solid var(--teal);display:flex;align-items:center;justify-content:center;text-align:center;font:700 12px/1.3 var(--head);color:var(--teal-dark)}
.nav{position:absolute;top:34px;font:500 14px var(--body);color:var(--ink)}
.nav a{position:absolute;white-space:nowrap;color:var(--ink);text-decoration:none}
.nav a.active{color:var(--teal)}

.hero-photo{left:0;top:87px;width:1200px;height:653px;background:linear-gradient(135deg,#e8e8e8,#8a8a8a 55%,#3c3c3c)}
.welcome-band{left:0;top:740px;width:1200px;height:174px;background:var(--band)}
.welcome-band h1{position:absolute;left:110px;top:28px;width:620px;font:700 29px/38px var(--head);color:var(--white);text-transform:uppercase}

/* about */
.about-ring{left:119px;top:1018px;width:460px;height:460px;border-radius:50%;border:7px solid var(--teal);display:flex;align-items:center;justify-content:center}
.about-ring div{width:406px;height:406px;border-radius:50%;background:radial-gradient(circle at 50% 40%,#c9a68d,#5e8f5a 70%,#2f8fbf)}
.section-title{font:800 36px var(--head);color:var(--ink);text-transform:uppercase}
.about-copy{left:657px;top:1128px;width:424px;font:400 13.5px/25px var(--body);text-align:justify;color:#666}

/* services */
.services{left:0;top:1582px;width:1200px;height:535px;background:var(--teal)}
.services h2{position:absolute;top:70px;width:100%;text-align:center;font:800 34px var(--head);color:var(--white)}
.service{position:absolute;top:170px;width:300px;text-align:center;color:var(--white)}
.service .ring{margin:0 auto;width:184px;height:184px;border-radius:50%;border:2px solid var(--orange);display:flex;align-items:center;justify-content:center}
.service .disc{width:154px;height:154px;border-radius:50%;background:var(--orange);display:flex;align-items:center;justify-content:center}
.service .disc svg{width:86px;height:86px}
.service h3{margin-top:28px;font:700 14.5px var(--body);text-transform:uppercase}
.service hr{width:34px;margin:12px auto 14px;border:0;border-top:2px solid var(--white)}
.service p{font:400 13.5px/21px var(--body)}

/* faq */
.faq-item{position:absolute;left:110px;width:478px;height:52px;border:1px solid #ddd;display:flex;align-items:center;justify-content:space-between;padding:0 6px 0 16px;font:400 15px var(--body);color:#555}
.faq-item i{width:50px;height:38px;background:#e6e6e6;display:flex;align-items:center;justify-content:center}
.faq-frame{left:658px;top:2235px;width:428px;height:427px;border:11px solid var(--teal);padding:12px;background:var(--white)}
.faq-frame div{width:100%;height:100%;background:linear-gradient(160deg,#6b5a46,#7a9a5b 55%,#8cbf6a)}

/* blog */
.blog{left:0;top:2772px;width:1200px;height:1086px;background:var(--orange)}
.blog h2{position:absolute;top:80px;width:100%;text-align:center;font:800 30px var(--head);color:var(--white)}
.card{position:absolute;background:var(--white)}
.card .photo{width:100%}
.card .body{padding:0 26px}
.card .date{font:400 11px var(--body);color:#666;margin-top:24px}
.card h4{font:700 14.5px var(--head);color:var(--ink);margin:8px 0 6px;text-transform:uppercase}
.card p{font:400 13px/19px var(--body);color:#666}
.card .more{display:inline-block;margin-top:18px;background:var(--teal);color:var(--white);font:700 10px var(--body);padding:6px 12px}
.feature{left:102px;top:174px;width:644px;height:415px;background:linear-gradient(150deg,#cfcfcf,#6f6f6f 45%,#2e2e2e)}
.feature .overlay{position:absolute;left:28px;right:28px;bottom:22px;color:var(--white)}
.feature .overlay small{font:400 12px var(--body)}
.feature .overlay h3{font:700 19px var(--head);margin:10px 0 12px;white-space:nowrap}
.feature .overlay p{font:400 14px/18px var(--body);color:var(--white)}

/* footer */
.site-footer{left:0;top:3858px;width:1200px;height:380px;background:var(--footer);color:var(--white)}
.foot-brand{position:absolute;left:173px;top:44px;width:190px;height:190px;border-radius:50%;border:4px solid var(--teal);display:flex;align-items:center;justify-content:center;text-align:center;font:700 17px/1.3 var(--head);color:var(--teal)}
.foot-col{position:absolute;top:58px;font:400 12px/16px var(--body)}
.foot-col h5{font:700 13px var(--body);margin-bottom:20px}
.foot-col ul{list-style:none}
.foot-col li{margin-bottom:14px}
.contact-row{display:flex;gap:14px;align-items:center;margin-bottom:18px}
.dot{width:24px;height:24px;border-radius:50%;background:var(--white);flex:none;display:flex;align-items:center;justify-content:center}
.dot svg{width:12px;height:12px}
.foot-rule{position:absolute;left:102px;top:287px;width:996px;border-top:1px solid #4a4a4a}
.copyright{position:absolute;top:330px;width:100%;text-align:center;font:400 13px var(--body)}
</style>
</head>
<body>

<header class="site-header">
  <nav class="nav">
    <a class="active" style="left:410px">HOME</a>
    <a style="left:484px">ABOUT</a>
    <a style="left:565px">SERVICES</a>
    <a style="left:663px">FAQS</a>
    <a style="left:731px">BLOG</a>
    <a style="left:800px">CONTACT</a>
  </nav>
  <a class="btn" style="left:934px;top:21px;width:150px;height:46px">GET STARTED
    <svg viewBox="0 0 16 16"><circle cx="8" cy="8" r="8" fill="#fff"/><path d="M6 4l4 4-4 4" stroke="#2fcec2" stroke-width="2" fill="none"/></svg></a>
</header>
<div class="brand"><span>Harborline<br>Families</span></div>

<div class="abs hero-photo" role="img" aria-label="Black and white photo of two parents holding their newborn"></div>

<section class="abs welcome-band">
  <h1>Congratulations on your birth &amp; welcome to Harborline Families Postpartum Care!</h1>
  <a class="btn" style="left:841px;top:57px;width:150px;height:46px">GET STARTED
    <svg viewBox="0 0 16 16"><circle cx="8" cy="8" r="8" fill="#fff"/><path d="M6 4l4 4-4 4" stroke="#2fcec2" stroke-width="2" fill="none"/></svg></a>
</section>

<div class="abs about-ring"><div role="img" aria-label="Portrait of the postpartum care expert outdoors"></div></div>
<h2 class="abs section-title" style="left:657px;top:1064px">About Us</h2>
<p class="abs about-copy">Hi, I'm Dana Reyes, a certified postpartum care expert and educator serving families of all varieties in the greater San Diego area and beyond. My passion as a professional is showing new parents just like you that whether you've just had your first child or your fifth, you can not only survive your postpartum period (also known as the 4th trimester), but you and your family can THRIVE – with the kind of compassionate, skilled, and targeted support for your unique needs that only an expert can provide. That's where I come in.</p>
<a class="btn" style="left:659px;top:1373px;width:150px;height:49px">LEARN MORE
  <svg viewBox="0 0 16 16"><circle cx="8" cy="8" r="8" fill="#fff"/><path d="M6 4l4 4-4 4" stroke="#2fcec2" stroke-width="2" fill="none"/></svg></a>

<section class="abs services">
  <h2>OUR SERVICES</h2>
  <div class="service" style="left:-12px">
    <div class="ring"><div class="disc"><svg viewBox="0 0 80 80" fill="#fff"><circle cx="40" cy="40" r="11"/><circle cx="14" cy="14" r="8"/><circle cx="66" cy="16" r="8"/><circle cx="12" cy="62" r="8"/><circle cx="66" cy="64" r="8"/><circle cx="40" cy="8" r="6"/><path d="M14 14L40 40M66 16L40 40M12 62L40 40M66 64L40 40M40 8V40" stroke="#fff" stroke-width="4"/></svg></div></div>
    <h3>Bonding &amp; Attachment</h3><hr><p>I enhance bonding and attachment<br>between parents(s) and baby</p>
  </div>
  <div class="service" style="left:296px">
    <div class="ring"><div class="disc"><svg viewBox="0 0 80 80"><circle cx="40" cy="40" r="34" fill="#fff"/><circle cx="44" cy="22" r="5" fill="#f77b4e"/><path d="M36 34h12l-6 24h6" stroke="#f77b4e" stroke-width="7" fill="none"/></svg></div></div>
    <h3>Practical Based Information</h3><hr><p>I provide practical, evidence-based<br>information about baby care</p>
  </div>
  <div class="service" style="left:602px">
    <div class="ring"><div class="disc"><svg viewBox="0 0 80 80"><path d="M40 70L10 40C0 28 6 10 22 10c8 0 14 5 18 10 4-5 10-10 18-10 16 0 22 18 12 30z" fill="#fff"/><path d="M6 40h22l6-10 8 20 6-10h26" stroke="#f77b4e" stroke-width="4" fill="none"/></svg></div></div>
    <h3>Mental &amp; Emotional Health</h3><hr><p>I prioritize the mental and emotional<br>health of parent(s) and help identify</p>
  </div>
  <div class="service" style="left:910px">
    <div class="ring"><div class="disc"><svg viewBox="0 0 80 80" fill="#fff"><circle cx="44" cy="14" r="8"/><rect x="36" y="24" width="16" height="20" rx="5"/><path d="M6 48l10-4 12 8h22c4 0 4 6 0 6H34h18l18-12c4-2 7 2 4 5L54 68H24L6 60z"/></svg></div></div>
    <h3>Hands-On Support</h3><hr><p>I offer hands-on support with<br>baby(ies), older siblings, pets</p>
  </div>
</section>

<h2 class="abs section-title" style="left:109px;top:2265px;line-height:40px;font-size:35px">Frequently Asked<br>Question</h2>
<div class="faq-item" style="top:2369px">What is a postpartum care expert (doula)?<i><svg width="12" height="8" viewBox="0 0 12 8"><path d="M0 0h12L6 8z" fill="#333"/></svg></i></div>
<div class="faq-item" style="top:2438px">Do you provide nanny services?<i><svg width="12" height="8" viewBox="0 0 12 8"><path d="M0 0h12L6 8z" fill="#333"/></svg></i></div>
<div class="faq-item" style="top:2506px">What kinds of medical support can you offer?<i><svg width="12" height="8" viewBox="0 0 12 8"><path d="M0 0h12L6 8z" fill="#333"/></svg></i></div>
<div class="faq-item" style="top:2575px">Are you available for overnight shifts?<i><svg width="12" height="8" viewBox="0 0 12 8"><path d="M0 0h12L6 8z" fill="#333"/></svg></i></div>
<div class="abs faq-frame"><div role="img" aria-label="Family of two parents and their daughter hugging by a tree in a park"></div></div>

<section class="abs blog">
  <h2>LATEST BLOG</h2>
  <article class="card feature" role="img" aria-label="Care expert with new parents holding their baby on a sofa">
    <div class="overlay"><small>Sep 02, 2021</small><h3>LOREM IPSUM IS SIMPLY DUMMY TEXT OF THE PRINTING</h3><p>Contrary to popular belief, Lorem Ipsum is not simply random text</p></div>
  </article>
  <article class="card" style="left:767px;top:174px;width:337px;height:415px">
    <div class="photo" style="height:244px;background:linear-gradient(160deg,#8a7c70,#c9b7a3)" role="img" aria-label="Care expert holding twin babies"></div>
    <div class="body"><h4 style="margin-top:14px">Lorem ipsum is simply dummy</h4><p>There are many variations of passages of Lorem Ipsum available, but the majority have suffered alteration</p><span class="more">READ MORE</span></div>
  </article>
  <article class="card" style="left:102px;top:611px;width:319px;height:380px">
    <div class="photo" style="height:200px;background:linear-gradient(160deg,#7a5a44,#c8a690)" role="img" aria-label="Care expert holding a newborn by a fireplace"></div>
    <div class="body"><div class="date">Sep 02, 2021</div><h4>Lorem ipsum is simply dummy</h4><p>There are many variations of passages of Lorem Ipsum available, but the.</p><span class="more">READ MORE</span></div>
  </article>
  <article class="card" style="left:444px;top:611px;width:320px;height:380px">
    <div class="photo" style="height:200px;background:linear-gradient(160deg,#bdb6ad,#6d6660)" role="img" aria-label="Care expert with new parents and their baby"></div>
    <div class="body"><div class="date">Sep 02, 2021</div><h4>Lorem ipsum is simply dummy</h4><p>There are many variations of passages of Lorem Ipsum available, but the.</p><span class="more">READ MORE</span></div>
  </article>
  <article class="card" style="left:787px;top:611px;width:319px;height:380px">
    <div class="photo" style="height:200px;background:linear-gradient(160deg,#dcdcdc,#4a4a4a)" role="img" aria-label="Black and white photo of parents with newborn"></div>
    <div class="body"><div class="date">Sep 02, 2021</div><h4>Lorem ipsum is simply dummy</h4><p>There are many variations of passages of Lorem Ipsum available, but the.</p><span class="more">READ MORE</span></div>
  </article>
</section>

<footer class="abs site-footer">
  <div class="foot-brand">Harborline<br>Families</div>
  <div class="foot-col" style="left:505px"><h5>MENU</h5>
    <ul><li>HOME</li><li>ABOUT US</li><li>SERVICES</li><li>BLOG</li><li>CONTACT US</li></ul></div>
  <div class="foot-col" style="left:690px"><h5>CONTACT US</h5>
    <div class="contact-row"><span class="dot"><svg viewBox="0 0 12 12"><path d="M6 0a4 4 0 0 1 4 4c0 3-4 8-4 8S2 7 2 4a4 4 0 0 1 4-4z" fill="#2fcec2"/></svg></span><span>42 Tidewater Lane<br>Seaport Bay, CA 90000</span></div>
    <div class="contact-row"><span class="dot"><svg viewBox="0 0 12 12"><path d="M2 1l3 0 1 3-2 1c1 2 2 3 3 3l1-2 3 1v3C6 11 1 6 2 1z" fill="#2fcec2"/></svg></span><span>Call Us<br>1 555 010 2040</span></div>
    <div class="contact-row"><span class="dot"><svg viewBox="0 0 12 12"><rect x="1" y="3" width="10" height="7" fill="#2fcec2"/><path d="M1 3l5 4 5-4" stroke="#fff" fill="none"/></svg></span><span>E mail Us<br>hello@harborlinefamilies.com</span></div>
  </div>
  <div class="foot-col" style="left:988px"><h5>FOLLOW US</h5>
    <div class="contact-row"><span class="dot"></span><span>Like us on<br>WAVEBOARD</span></div>
    <div class="contact-row"><span class="dot"></span><span>Follow us on<br>TIDECAST</span></div>
    <div class="contact-row"><span class="dot"></span><span>Follow us on<br>HARBORNET</span></div>
  </div>
  <div class="foot-rule"></div>
  <p class="copyright">Copyright © 2021 Harborline Families.All Rights Reserved</p>
</footer>

</body>
</html>
```